Mira Bloom Fitness Coaching Project

I am a personal trainer based in London. My services include one-on-one PT sessions, bootcamps.
I would like the design to be minimalistic. With light colours: white, pink, purple.
I specialise in weight loss, flexibility, mobility.

Tessa Brogan
Personal Trainer
Email: tessa.brogan@quellmail.com
tel: 07700218493
Instagram: Mira Bloom

Target Market(s)

adults, mostly females (age 18-50).

Industry/Entity Type

Fitness

Contact Information for Business Card

Tessa Brogan
Personal Trainer
tel: 07700218493
Instagram: Mira Bloom

Font styles to use
Serif

Colors
eea4c8
fbd4d5
fdf9cf
cfeae6
cee9f5

Requirements
Nice to have
• minimalistic style
• easy to read and remember

```html
<!DOCTYPE html>
<html lang="en">
<head>
<meta charset="utf-8">
<title>Tessa Brogan – Personal Trainer Business Card</title>
<link rel="stylesheet" href="https://fonts.googleapis.com/css2?family=Cormorant+Garamond:wght@500;600&display=swap">
<style>
  :root {
    --stage: #f4f1ee;
    --card-white: #ffffff;
    --ink-plum: #a05c8c;
    --frame-mint: #cfeae6;
    --blush-pink: #eea4c8;
    --soft-rose: #fbd4d5;
    --cream: #fdf9cf;
    --mint: #cfeae6;
    --sky: #cee9f5;
    --name-white: #ffffff;
  }
  * { box-sizing: border-box; margin: 0; padding: 0; }
  html, body {
    width: 1200px;
    height: 960px;
    overflow: hidden;
    background: var(--stage);
    font-family: "Cormorant Garamond", "Garamond", serif;
  }
  .canvas {
    position: relative;
    width: 1200px;
    height: 960px;
  }

  /* Contact side */
  .card-contact {
    position: absolute;
    left: 144px;
    top: 127px;
    width: 406px;
    height: 707px;
    background: var(--card-white);
    box-shadow: 0 2px 6px rgba(0,0,0,0.10);
    color: var(--ink-plum);
    text-align: center;
  }
  .contact-name {
    position: absolute;
    top: 236px;
    left: 0;
    width: 100%;
    font-size: 30px;
    font-weight: 600;
    letter-spacing: 3.5px;
    line-height: 34px;
  }
  .contact-role {
    position: absolute;
    top: 273px;
    left: 0;
    width: 100%;
    font-size: 19px;
    font-weight: 500;
    letter-spacing: 2.6px;
    line-height: 22px;
  }
  .divider {
    position: absolute;
    top: 326px;
    left: 189px;
    width: 29px;
    height: 3px;
    background: var(--ink-plum);
  }
  .icon-row {
    position: absolute;
    top: 361px;
    left: 0;
    width: 100%;
    display: flex;
    justify-content: center;
    gap: 10px;
    color: var(--ink-plum);
  }
  .icon-row svg { width: 14px; height: 14px; display: block; }
  .contact-details {
    position: absolute;
    top: 398px;
    left: 0;
    width: 100%;
    list-style: none;
    font-size: 20px;
    font-weight: 600;
    letter-spacing: 2.4px;
    line-height: 26px;
  }
  .contact-details .phone { font-size: 21px; letter-spacing: 3.2px; }

  /* Photo side */
  .card-photo {
    position: absolute;
    left: 606px;
    top: 128px;
    width: 420px;
    height: 719px;
    background: var(--frame-mint);
    box-shadow: 0 2px 6px rgba(0,0,0,0.10);
    padding: 9px;
  }
  .photo-area {
    position: relative;
    width: 100%;
    height: 100%;
    background: linear-gradient(180deg,
      var(--blush-pink) 0%,
      var(--soft-rose) 38%,
      var(--mint) 46%,
      var(--sky) 66%,
      var(--cream) 90%,
      var(--soft-rose) 100%);
  }
  .photo-name {
    position: absolute;
    top: 344px;
    left: 9px;
    width: 402px;
    text-align: center;
    color: var(--name-white);
    font-size: 40px;
    font-weight: 600;
    letter-spacing: 4px;
    line-height: 44px;
    padding-left: 24px;
    white-space: nowrap;
  }
  .photo-name-band {
    position: absolute;
    top: 340px;
    left: 9px;
    width: 402px;
    height: 52px;
    background: var(--blush-pink);
    opacity: 0.85;
  }
</style>
</head>
<body>
<main class="canvas">
  <section class="card-contact" aria-label="Contact side of business card">
    <h1 class="contact-name">Tessa Brogan</h1>
    <p class="contact-role">Personal Trainer</p>
    <div class="divider"></div>
    <div class="icon-row" aria-hidden="true">
      <svg viewBox="0 0 14 14" class="icon-phone">
        <path d="M3 1.5 L5 4 L4 5.5 C4.8 7.3 6.5 9 8.5 10 L10 9 L12.5 11 L11 12.8 C6.5 12.5 1.5 7.5 1.2 3 Z" fill="none" stroke="currentColor" stroke-width="1.2" stroke-linejoin="round"/>
      </svg>
      <svg viewBox="0 0 14 14" class="icon-mail">
        <rect x="1" y="3" width="12" height="8.5" fill="none" stroke="currentColor" stroke-width="1.2"/>
        <path d="M1 3 L7 8 L13 3" fill="none" stroke="currentColor" stroke-width="1.2"/>
      </svg>
      <svg viewBox="0 0 14 14" class="icon-social">
        <circle cx="7" cy="7" r="4" fill="currentColor"/>
      </svg>
    </div>
    <ul class="contact-details">
      <li class="phone">07700218493</li>
      <li class="email">tessa.brogan@quellmail.com</li>
      <li class="social">Mira Bloom</li>
    </ul>
  </section>

  <section class="card-photo" aria-label="Photo side of business card">
    <div class="photo-area" role="img" aria-label="Photo of the trainer leaping in a split jump in front of a painted street mural"></div>
    <div class="photo-name-band" aria-hidden="true"></div>
    <h2 class="photo-name">TESSA BROGAN</h2>
  </section>
</main>
</body>
</html>
```